We are a recruitment company based in Norwich/Cambridge England.
I have included our company logo which we want to remain the same.

What we are looking for is a new creative Business card which will really stand out!!

Contact Information for Business Card

Harriet Dunmore
email: Harriet@plavex.co.uk
Address: Brackwell House
Fenmoor Enterprise Park
Partridge Way
Norwich
QB9 3KX
Tel:01632 960418

```html
<!DOCTYPE html>
<html lang="en">
<head>
<meta charset="utf-8">
<title>Plavex Business Card</title>
<link rel="stylesheet" href="https://fonts.googleapis.com/css2?family=Arimo:wght@400;700&display=swap">
<style>
  :root {
    --bg: #2b2b2d;
    --green: #8cc63f;
    --green-soft: #97cc4f;
    --white: #ffffff;
    --grey: #8a878d;
    --text-grey: #6f6f73;
  }
  * { margin: 0; padding: 0; box-sizing: border-box; }
  html, body {
    width: 1200px;
    height: 1189px;
    overflow: hidden;
    background: var(--bg);
    font-family: "Arimo", Arial, sans-serif;
  }
  .sheet {
    position: relative;
    width: 1200px;
    height: 1189px;
  }
  .card {
    position: absolute;
    left: 150px;
    width: 900px;
    height: 515px;
    border-radius: 34px;
    overflow: hidden;
  }

  /* Front */
  .card--front {
    top: 60px;
    background: var(--green);
  }
  .front__halo {
    position: absolute;
    left: 250px;
    top: 40px;
    width: 440px;
    height: 440px;
    border-radius: 50%;
    background: var(--green-soft);
  }
  .front__brand {
    position: absolute;
    left: 0;
    right: 0;
    top: 168px;
    display: flex;
    justify-content: center;
    align-items: center;
    gap: 26px;
  }
  .brand__dot {
    width: 96px;
    height: 96px;
    border-radius: 50%;
    background: var(--white);
  }
  .brand__text { color: var(--white); }
  .brand__name {
    font-weight: 700;
    font-size: 92px;
    line-height: 0.95;
    letter-spacing: -1px;
  }
  .brand__tagline {
    font-size: 15px;
    letter-spacing: 6px;
    margin-top: 6px;
  }
  .front__web {
    position: absolute;
    left: 0;
    right: 0;
    top: 352px;
    text-align: center;
    color: var(--white);
    font-size: 20px;
    letter-spacing: 5px;
  }

  /* Back */
  .card--back {
    top: 615px;
    background: var(--white);
  }
  .back__tab {
    position: absolute;
    left: -22px;
    top: 78px;
    width: 44px;
    height: 44px;
    border-radius: 50%;
    background: var(--green);
  }
  .contact {
    position: absolute;
    left: 62px;
    top: 64px;
    color: var(--text-grey);
  }
  .contact__name {
    color: var(--green);
    font-weight: 700;
    font-size: 33px;
    line-height: 1;
  }
  .contact__role {
    font-size: 22px;
    line-height: 1.1;
  }
  .contact__address {
    margin-top: 84px;
    font-size: 21px;
    line-height: 1.3;
  }
  .contact__lines {
    list-style: none;
    margin-top: 36px;
    font-size: 24px;
  }
  .contact__lines li {
    display: flex;
    align-items: center;
    gap: 14px;
    height: 34px;
  }
  .contact__icon { width: 28px; height: 28px; flex: none; }

  .back__mark {
    position: absolute;
    right: 60px;
    top: 90px;
    display: flex;
    align-items: center;
    gap: 20px;
  }
  .mark__circle {
    width: 100px;
    height: 100px;
    border-radius: 50%;
    background: var(--grey);
  }
  .mark__name {
    color: var(--green);
    font-weight: 700;
    font-size: 60px;
    letter-spacing: -1px;
    white-space: nowrap;
  }
</style>
</head>
<body>
<main class="sheet">

  <section class="card card--front" aria-label="Card front">
    <div class="front__halo"></div>
    <div class="front__brand">
      <div class="brand__dot"></div>
      <div class="brand__text">
        <div class="brand__name">Plavex</div>
        <div class="brand__tagline">Technology Recruitment</div>
      </div>
    </div>
    <div class="front__web">www.plavex.co.uk</div>
  </section>

  <section class="card card--back" aria-label="Card back">
    <div class="back__tab"></div>
    <div class="contact">
      <div class="contact__name">Harriet Dunmore</div>
      <div class="contact__role">CEO</div>
      <div class="contact__address">Brackwell House, Fenmoor Enterprise Park<br>Partridge Way, Norwich QB9 3KX</div>
      <ul class="contact__lines">
        <li>
          <svg class="contact__icon" viewBox="0 0 28 28" aria-hidden="true">
            <circle cx="14" cy="14" r="12.5" fill="none" stroke="#8cc63f" stroke-width="2"/>
            <rect x="9.5" y="7" width="9" height="14" rx="1.5" fill="none" stroke="#8cc63f" stroke-width="2"/>
          </svg>
          01632 960418
        </li>
        <li>
          <svg class="contact__icon" viewBox="0 0 28 28" aria-hidden="true">
            <circle cx="14" cy="14" r="12.5" fill="none" stroke="#8cc63f" stroke-width="2"/>
            <rect x="7.5" y="9" width="13" height="10" fill="#8cc63f"/>
            <path d="M7.5 9 L14 15 L20.5 9" fill="none" stroke="#ffffff" stroke-width="1.5"/>
          </svg>
          Harriet@plavex.co.uk
        </li>
        <li>
          <svg class="contact__icon" viewBox="0 0 28 28" aria-hidden="true">
            <circle cx="14" cy="14" r="12.5" fill="none" stroke="#8cc63f" stroke-width="2"/>
            <circle cx="14" cy="14" r="7" fill="none" stroke="#8cc63f" stroke-width="1.5"/>
            <path d="M7 14 H21 M14 7 V21 M9 10 H19 M9 18 H19" stroke="#8cc63f" stroke-width="1.2"/>
          </svg>
          www.plavex.co.uk
        </li>
      </ul>
    </div>
    <div class="back__mark">
      <div class="mark__circle"></div>
      <div class="mark__name">Plavex</div>
    </div>
  </section>

</main>
</body>
</html>
```